1 Dimensional cover for digital product

Please note that if a designer comes in with an original design and other designers try to copy them too closely I will always work with the original designer in order to get the actual look I want.
Therefore it is in the interests of the designers to get their concepts in first.

I am designing some audio products for football (soccer players).

I would like a square version and a 16:9 version of the packaging completed. The square version will be for the Sonvia audio cover and the 16:9 for the thumbnails of videos.

I would like the final images in PSP files as a template that I can change the title and the main image.

I am open to creativity in this project but would like it to be a luxury and premium in what it is portraying.

I have added my logo and also the packaging that I currently use on my sister website which is not aimed at football, soccer.

I've also included an image of one of my models. This would NOT be the product image, but it could be a background image, or you may choose to leave it out altogether.

I've also included an example image as the main product image.

Although I have chosen greyscale I would also like to see products with colour.

The product page is at https://kelvarn.global/collections/all
I add this so that you can chose any one of the titles for this template

Target Market(s)

This is aimed at professional footballers

Industry/Entity Type

Sporting Good

Font styles to use
Serif
Sans Serif

Colors

Designer to choose colors to be used in the design.

Requirements
Must have
• This must look like it is made for an affluent market.
• It may also be simple in its design but I do not wish to be too prescriptive with creativity.
• My typography is Montserrat
Nice to have
• Can include the colors of my logos:
• #5BA9DE
• #272B5F
• Or you can choose to go with greyscale
Should not have
• This is a product for serious athletes so it should look very professional and adult orientated (so not cartoonish its look)

```html
<!DOCTYPE html>
<html lang="en">
<head>
<meta charset="utf-8">
<title>After Game – Hypnosis Sessions</title>
<link href="https://fonts.googleapis.com/css2?family=Montserrat:wght@300;400;600;800&display=swap" rel="stylesheet">
<style>
  :root {
    --navy: #272b5f;
    --sky: #5ba9de;
    --amber: #e8a71f;
    --amber-deep: #e39d24;
    --sun: #f6d21f;
    --gold-text: #b9a45b;
    --paper: #ffffff;
    --photo-dark: #2b2a24;
    --photo-mid: #6d6a58;
    --photo-light: #c9c4a6;
  }
  * { margin: 0; padding: 0; box-sizing: border-box; }
  html, body { width: 1200px; height: 675px; overflow: hidden; background: var(--paper); }
  .cover {
    position: relative;
    width: 1200px;
    height: 675px;
    overflow: hidden;
    background: var(--paper);
    font-family: "Montserrat", sans-serif;
  }
  .cover__shapes { position: absolute; inset: 0; }
  .brand {
    position: absolute;
    left: 63px;
    top: 46px;
    width: 172px;
    text-align: center;
    color: var(--paper);
  }
  .brand__dot {
    display: block;
    width: 34px;
    height: 34px;
    margin: 0 auto 20px;
    border-radius: 50%;
    background: var(--paper);
  }
  .brand__name {
    font-size: 8.6px;
    font-weight: 600;
    letter-spacing: 0.04em;
    text-transform: uppercase;
    white-space: nowrap;
  }
  .brand__line {
    display: flex;
    align-items: center;
    gap: 6px;
    margin-top: 3px;
    font-size: 11px;
    font-weight: 400;
    letter-spacing: 0.08em;
    text-transform: uppercase;
  }
  .brand__line::before, .brand__line::after {
    content: "";
    flex: 1;
    height: 1px;
    background: var(--paper);
  }
  .kicker {
    position: absolute;
    right: 697px;
    top: 232px;
    font-size: 19px;
    font-weight: 600;
    color: var(--gold-text);
    white-space: nowrap;
  }
  .title {
    position: absolute;
    right: 697px;
    top: 254px;
    text-align: right;
    font-size: 124px;
    font-weight: 800;
    line-height: 102px;
    letter-spacing: -0.01em;
    color: var(--sky);
    text-transform: uppercase;
  }
  .tagline {
    position: absolute;
    left: 160px;
    top: 558px;
    font-size: 13.5px;
    font-weight: 300;
    line-height: 17px;
    letter-spacing: 0.02em;
    color: var(--gold-text);
    text-transform: uppercase;
  }
</style>
</head>
<body>
<main class="cover">
  <svg class="cover__shapes" width="1200" height="675" viewBox="0 0 1200 675" xmlns="http://www.w3.org/2000/svg">
    <defs>
      <linearGradient id="photo-tone" x1="0" y1="0" x2="1" y2="1">
        <stop offset="0" stop-color="var(--photo-dark)"/>
        <stop offset="0.55" stop-color="var(--photo-mid)"/>
        <stop offset="1" stop-color="var(--photo-light)"/>
      </linearGradient>
      <filter id="frame-shadow" x="-10%" y="-10%" width="120%" height="120%">
        <feDropShadow dx="0" dy="0" stdDeviation="6" flood-color="#000" flood-opacity="0.18"/>
      </filter>
    </defs>

    <polygon class="corner-band" points="0,0 374,0 0,374" fill="var(--navy)"/>

    <polygon class="accent accent--amber-strip" points="629,250 662,268 662,540 629,557" fill="var(--amber)"/>
    <polygon class="accent accent--amber-top" points="987,173 1114,246 987,272" fill="var(--amber)"/>
    <polygon class="accent accent--navy-small" points="1125,268 1125,306 1090,285" fill="var(--navy)"/>
    <polygon class="accent accent--sun-right" points="1125,338 1195,380 1125,419" fill="var(--sun)"/>
    <polygon class="accent accent--navy-large" points="942,433 1125,340 1125,539" fill="var(--navy)"/>
    <polygon class="accent accent--amber-low" points="768,535 857,433 1023,484 853,577" fill="var(--amber-deep)"/>
    <polygon class="accent accent--sun-low" points="770,624 770,535 853,577" fill="var(--sun)"/>

    <polygon class="accent accent--sky-pointer" points="524,316 605,270 605,363" fill="var(--sky)"/>

    <polygon class="photo-frame" points="663,52 1138,321 663,590" fill="var(--paper)" filter="url(#frame-shadow)"/>
    <polygon class="photo-area" points="676,66 1114,321 676,570" fill="url(#photo-tone)" role="img" aria-label="Sepia action photograph of two footballers leaping for the ball under stadium lights"/>

    <polygon class="accent accent--tagline-marker" points="98,541 146,567 98,594" fill="var(--amber)"/>
  </svg>

  <div class="brand">
    <span class="brand__dot"></span>
    <p class="brand__name">Elric Vantor Hypnotherapy</p>
    <p class="brand__line">Kelvarn</p>
  </div>

  <p class="kicker">Hypnosis sessions</p>
  <h1 class="title">After<br>Game</h1>
  <p class="tagline">Conditioning you towards<br>even better future performances.</p>
</main>
</body>
</html>
```